Veltra Metrics New Website for Health Benefits Plan Decisioneering Tool Launch

Veltra Metrics is a SaaS provider of health benefits comparison tools. We need a new simple SaaS focused website to direct customers to our product

Target Market(s)

General Public comparing their health benefits plans from their employer or from the state exchanges in the US

Coding

Coded - Design and coding required

Number of Pages Required

3 page

Requirements
Must have
• Main page - "Know the Best Health Benefits Plan for You!"
Graphic of a person looking over papers on their desk
Compare Now button to link to SaaS product
About Us
Product Page

https://plimbo.example/top-app-pages/

```html
<!DOCTYPE html>
<html lang="en">
<head>
<meta charset="utf-8">
<title>Veltra Metrics – Website Design</title>
<link href="https://fonts.googleapis.com/css2?family=Alegreya:wght@400;500;700&family=Source+Sans+3:wght@400;600&display=swap" rel="stylesheet">
<style>
:root{
  --bg:#2a95d6;
  --blue:#2f92d5;
  --ink:#1c1c1c;
  --muted:#7a8590;
  --band:#e3f2fb;
  --card:#dff0fb;
  --line:#c9d6e0;
  --white:#ffffff;
}
*{margin:0;padding:0;box-sizing:border-box}
h1,h2,h3,h4{font-weight:400}
html,body{width:1200px;height:2352px;overflow:hidden;background:var(--bg)}
.stage{position:relative;width:1314px;height:2576px;transform:scale(0.91324);transform-origin:0 0;background:var(--bg);font-family:"Source Sans 3",sans-serif;color:var(--ink)}
.brand-title{position:absolute;left:62px;top:255px;width:505px;text-align:center;font-family:"Alegreya",serif;font-weight:400;font-size:60px;line-height:70px;letter-spacing:2px;color:var(--white)}
.brand-sub{position:absolute;left:60px;top:330px;width:506px;display:flex;align-items:center;gap:12px;font-family:"Alegreya",serif;font-size:36px;letter-spacing:10px;color:var(--white)}
.brand-sub::before,.brand-sub::after{content:"";flex:1;height:3px;background:var(--white)}
.screen{position:absolute;left:615px;top:87px;width:576px;height:365px;background:var(--white);overflow:hidden}
.page{position:absolute;top:535px;width:590px;height:1985px;background:var(--white);overflow:hidden}
.page--illustrated{left:58px}
.page--photo{left:668px}
.abs{position:absolute}
.serif{font-family:"Alegreya",serif}
.nav-logo{left:47px;top:13px;font-family:"Alegreya",serif;font-size:13px;color:var(--blue);letter-spacing:.3px}
.nav-links{left:188px;top:22px;display:flex;gap:12px;font-size:7.5px;font-weight:600;letter-spacing:.3px}
.btn{background:var(--blue);color:var(--white);font-family:"Alegreya",serif;font-weight:700;font-size:7.5px;letter-spacing:.3px;display:flex;align-items:center;justify-content:center}
.hero-art{left:15px;top:70px;width:275px;height:180px;border-radius:4px}
.page--photo .hero-art{left:28px;top:58px;width:272px;height:238px;border-radius:0}
.hero-title{left:331px;top:98px;font-family:"Alegreya",serif;font-weight:400;font-size:29px;line-height:30px;color:var(--ink)}
.hero-title .accent{color:var(--blue)}
.hero-text{left:331px;top:205px;font-size:7px;color:#333}
.label{font-size:7.5px;font-weight:600;color:var(--blue);letter-spacing:.4px;text-align:center;width:100%;left:0}
.section-title{width:100%;left:0;text-align:center;font-family:"Alegreya",serif;font-weight:400;font-size:16px;line-height:21px}
.benefits{left:55px;top:421px;display:flex;gap:5px}
.benefit{width:116px;height:103px;background:var(--card);text-align:center;padding-top:9px}
.benefit--active{background:var(--blue);color:var(--white)}
.benefit h3{font-family:"Alegreya",serif;font-weight:700;font-size:7.5px;margin-top:4px}
.benefit p{font-size:6.3px;line-height:15px;color:var(--muted);margin-top:1px}
.benefit--active p{color:#e6f3fc}
.band{left:0;width:590px;background:var(--band)}
.about-title{left:46px;top:630px;font-family:"Alegreya",serif;font-weight:400;font-size:16px;line-height:21px}
.about-text{left:46px;top:680px;width:220px;font-size:6.6px;line-height:14.8px;color:var(--muted)}
.about-art{left:270px;top:605px;width:298px;height:200px}
.page--photo .about-art{left:298px;top:618px;width:248px;height:188px}
.services{left:55px;top:972px;display:flex;gap:9px}
.service{width:154px;height:206px;background:var(--card)}
.service-art{width:154px;height:95px}
.service h3{font-family:"Alegreya",serif;font-weight:700;font-size:7.5px;line-height:15px;padding:6px 8px 0}
.service p{font-size:6.3px;line-height:15px;color:var(--muted);padding:3px 8px 0}
.service a{display:block;font-size:6.8px;font-weight:600;color:var(--blue);padding:2px 8px;text-decoration:none}
.chevron{top:1040px}
.avatar{left:105px;top:1325px;width:66px;height:66px;border-radius:50%}
.quote{left:202px;top:1325px;width:300px;font-size:6.6px;line-height:15px;color:#333}
.quote-name{left:204px;top:1386px;font-size:6.8px;font-weight:600;color:var(--blue);letter-spacing:.4px}
.dot{left:524px;width:5px;height:5px;border-radius:50%;background:var(--blue)}
.dot--open{background:transparent;border:1px solid var(--blue)}
.faq{left:56px;top:1533px;display:grid;grid-template-columns:238px 238px;gap:4px 3px}
.faq-item{height:30px;border:1px solid var(--line);display:flex;align-items:center;justify-content:space-between;padding:0 8px;font-family:"Alegreya",serif;font-size:7.2px;color:#333;background:var(--white)}
.subscribe{left:55px;top:1747px;width:480px;height:65px;background:var(--blue)}
.subscribe-title{left:34px;top:13px;font-family:"Alegreya",serif;font-weight:700;font-size:15px;line-height:19px;color:var(--white);letter-spacing:.6px}
.subscribe-field{left:167px;top:16px;width:280px;height:32px;background:var(--blue);border:1px solid #9fd0ef;display:flex}
.subscribe-field span{flex:1;color:#dcefff;font-size:7px;padding-left:12px;display:flex;align-items:center}
.subscribe-field i{width:60px;background:var(--white);display:flex;align-items:center;justify-content:center}
.footer-brand{left:47px;top:1880px;font-family:"Alegreya",serif;font-size:14px;color:var(--blue)}
.footer-col h4{font-family:"Alegreya",serif;font-weight:700;font-size:7.5px;margin-bottom:4px}
.footer-col li{list-style:none;font-size:7px;line-height:14px;color:#333}
.footer-col li b{color:var(--blue);font-weight:400;margin-right:4px}
.footer-contact li{display:flex;gap:5px;align-items:flex-start}
.footer-rule{left:37px;top:1940px;width:516px;height:1px;background:var(--line)}
.copyright{left:0;width:590px;top:1948px;text-align:center;font-family:"Alegreya",serif;font-size:6.2px;color:#333}
</style>
</head>
<body>
<div class="stage">
  <div class="brand-title">VELTRA METRICS</div>

  <!-- Hero screen preview -->
  <section class="screen">
    <div class="abs nav-logo" style="left:32px;top:13px">VELTRA METRICS</div>
    <nav class="abs nav-links" style="left:173px;top:21px"><span>HOME</span><span>ABOUT US</span><span>SERVICES</span><span>BENEFITS</span><span>CONTACT US</span></nav>
    <div class="abs btn" style="left:446px;top:12px;width:75px;height:24px">COMPARE NOW</div>
    <div class="abs hero-art" role="img" aria-label="Illustration of a person at a desk looking over stacks of paperwork" style="left:28px;top:75px;width:248px;height:170px;background:linear-gradient(135deg,#d6ecfb,#8cc8f0 60%,#2f6fd0)"></div>
    <h1 class="abs hero-title" style="left:316px;top:98px">Know the Best<br><span class="accent">Health Benefits</span><br>Plan for You!</h1>
    <p class="abs hero-text" style="left:316px;top:204px">Lorem ipsum dolor sit amet, consectetur adipiscing elit,</p>
    <div class="abs btn" style="left:317px;top:227px;width:75px;height:24px">GET STARTED</div>
    <div class="abs label" style="top:339px">OUR BENEFITS</div>
    <h2 class="abs section-title" style="top:353px">Lorem ipsum dolor sit amet, consectetur adipiscing</h2>
  </section>

  <!-- Page variant: illustrated -->
  <section class="page page--illustrated">
    <div class="abs nav-logo">VELTRA METRICS</div>
    <nav class="abs nav-links"><span>HOME</span><span>ABOUT US</span><span>SERVICES</span><span>BENEFITS</span><span>CONTACT US</span></nav>
    <div class="abs btn" style="left:460px;top:14px;width:75px;height:24px">COMPARE NOW</div>

    <div class="abs hero-art" role="img" aria-label="Illustration of a person at a desk looking over stacks of paperwork" style="background:linear-gradient(135deg,#d6ecfb,#8cc8f0 60%,#2f6fd0)"></div>
    <h1 class="abs hero-title">Know the Best<br><span class="accent">Health Benefits</span><br>Plan for You!</h1>
    <p class="abs hero-text">Lorem ipsum dolor sit amet, consectetur adipiscing elit,</p>
    <div class="abs btn" style="left:332px;top:229px;width:75px;height:24px">GET STARTED</div>

    <div class="abs label" style="top:342px">OUR BENEFITS</div>
    <h2 class="abs section-title" style="top:355px">Lorem ipsum dolor sit amet, consectetur adipiscing<br>elit, sed do eiusmod tempor incidi.</h2>
    <div class="abs benefits">
      <div class="benefit"><svg width="28" height="24" viewBox="0 0 28 24" fill="none" stroke="#5aa8df" stroke-width="1.2"><path d="M6 14a5 5 0 0 1 2-9 7 7 0 0 1 13 2 4 4 0 0 1 1 7"/><rect x="8" y="12" width="14" height="9"/><path d="M11 16h8"/></svg><h3>LOREM IPSUM DOLOR</h3><p>Lorem ipsum dolor sit amet<br>consectetur adipiscing elit,<br>sed do eiusmod tem.</p></div>
      <div class="benefit benefit--active"><svg width="28" height="24" viewBox="0 0 28 24" fill="none" stroke="#ffffff" stroke-width="1.2"><path d="M6 14a5 5 0 0 1 2-9 7 7 0 0 1 13 2 4 4 0 0 1 1 7"/><rect x="8" y="12" width="14" height="9"/><path d="M11 16h8"/></svg><h3>LOREM IPSUM DOLOR</h3><p>Lorem ipsum dolor sit amet<br>consectetur adipiscing elit,<br>sed do eiusmod tem.</p></div>
      <div class="benefit"><svg width="28" height="24" viewBox="0 0 28 24" fill="none" stroke="#5aa8df" stroke-width="1.2"><path d="M6 14a5 5 0 0 1 2-9 7 7 0 0 1 13 2 4 4 0 0 1 1 7"/><rect x="8" y="12" width="14" height="9"/><path d="M11 16h8"/></svg><h3>LOREM IPSUM DOLOR</h3><p>Lorem ipsum dolor sit amet<br>consectetur adipiscing elit,<br>sed do eiusmod tem.</p></div>
      <div class="benefit"><svg width="28" height="24" viewBox="0 0 28 24" fill="none" stroke="#5aa8df" stroke-width="1.2"><path d="M6 14a5 5 0 0 1 2-9 7 7 0 0 1 13 2 4 4 0 0 1 1 7"/><rect x="8" y="12" width="14" height="9"/><path d="M11 16h8"/></svg><h3>LOREM IPSUM DOLOR</h3><p>Lorem ipsum dolor sit amet<br>consectetur adipiscing elit,<br>sed do eiusmod tem.</p></div>
    </div>

    <div class="abs band" style="top:572px;height:283px"></div>
    <div class="abs label" style="top:617px;left:46px;width:auto;text-align:left">ABOUT VELTRA METRICS</div>
    <h2 class="abs about-title">Lorem ipsum dolor sit amet cons<br>ectetur adipiscing elit sed do.</h2>
    <p class="abs about-text">Lorem ipsum dolor sit amet, consectetur adipiscing elit, sed do eiusmod tempor incididunt ut labore et dolore magna aliqua. Ut enim ad minim veniam, quis nostrud exercitation ullamco laboris nisi ut aliquip ex ea commodo consequat. Duis aute irure dolor in reprehenderit in voluptate velit esse cillum dolore eu fugiat nulla pariatur.</p>
    <div class="abs btn" style="left:46px;top:783px;width:75px;height:24px">READ MORE</div>
    <div class="abs about-art" role="img" aria-label="Illustration of a person working at a computer desk beside a plant" style="background:linear-gradient(180deg,#bfe6f7,#5dd2f0 55%,#1c2a9a)"></div>

    <div class="abs label" style="top:900px">OUR SERVICES</div>
    <h2 class="abs section-title" style="top:913px">Lorem ipsum dolor sit amet, consectetur adipiscing<br>elit, sed do eiusmod tempor incidi.</h2>
    <svg class="abs chevron" style="left:16px" width="18" height="30" viewBox="0 0 18 30" fill="none" stroke="#333" stroke-width="1.3"><path d="M15 2 3 15l12 13"/></svg>
    <svg class="abs chevron" style="left:556px" width="18" height="30" viewBox="0 0 18 30" fill="none" stroke="#333" stroke-width="1.3"><path d="M3 2l12 13L3 28"/></svg>
    <div class="abs services">
      <div class="service"><div class="service-art" role="img" aria-label="Illustration of people reviewing a large document" style="background:linear-gradient(135deg,#e6f5fc,#8fd8e8)"></div><h3>LOREM IPSUM DOLOR SIT AMET CO<br>NSECTETUR ADIPISCING ELIT</h3><p>Lorem ipsum dolor si amet consectetur<br>adipiscing elit, sed do eiusmod tempor<br>incididunt ut labore et dolore magna.</p><a>READ MORE</a></div>
      <div class="service"><div class="service-art" role="img" aria-label="Illustration of a team collaborating around a laptop" style="background:linear-gradient(135deg,#eef7fc,#e98a6a 55%,#3b6fb8)"></div><h3>LOREM IPSUM DOLOR SIT AMET CO<br>NSECTETUR ADIPISCING ELIT</h3><p>Lorem ipsum dolor si amet consectetur<br>adipiscing elit, sed do eiusmod tempor<br>incididunt ut labore et dolore magna.</p><a>READ MORE</a></div>
      <div class="service"><div class="service-art" role="img" aria-label="Illustration of a group working together at a table" style="background:linear-gradient(135deg,#e3f3fc,#7cc6ea 60%,#2c6fb5)"></div><h3>LOREM IPSUM DOLOR SIT AMET CO<br>NSECTETUR ADIPISCING ELIT</h3><p>Lorem ipsum dolor si amet consectetur<br>adipiscing elit, sed do eiusmod tempor<br>incididunt ut labore et dolore magna.</p><a>READ MORE</a></div>
    </div>

    <div class="abs band" style="top:1224px;height:216px"></div>
    <div class="abs label" style="top:1270px;left:267px;width:auto">TESTIMONIALS</div>
    <h2 class="abs serif" style="left:198px;top:1286px;font-size:16px">What Our People are saying</h2>
    <div class="abs avatar" role="img" aria-label="Illustrated portrait of a customer" style="background:linear-gradient(135deg,#f6c89a,#3f63b6)"></div>
    <p class="abs quote">"Lorem ipsum dolor sit amet, consectetur adipiscing elit, sed do eiusmod tempor incididunt ut labore et dolore magna aliqua. Ut enim ad minim veniam, quis nostrud exercitation ullamco laboris nisi ut aliquip ex ea commodo consequat. Duis aute irure dolor in reprehenderit in voluptate velit esse."</p>
    <div class="abs quote-name">RINA CALDER</div>
    <div class="abs dot" style="top:1331px"></div><div class="abs dot dot--open" style="top:1346px"></div><div class="abs dot" style="top:1361px"></div>

    <div class="abs label" style="top:1485px">FAQ</div>
    <h2 class="abs section-title" style="top:1499px">Most asked questions</h2>
    <div class="abs faq">
      <div class="faq-item"><span>Lorem ipsum dolor sit amet, consectetur ?</span><span>+</span></div><div class="faq-item"><span>Lorem ipsum dolor sit amet, consectetur ?</span><span>+</span></div>
      <div class="faq-item"><span>Lorem ipsum dolor sit amet, consectetur ?</span><span>+</span></div><div class="faq-item"><span>Lorem ipsum dolor sit amet, consectetur ?</span><span>+</span></div>
      <div class="faq-item"><span>Lorem ipsum dolor sit amet, consectetur ?</span><span>+</span></div><div class="faq-item"><span>Lorem ipsum dolor sit amet, consectetur ?</span><span>+</span></div>
      <div class="faq-item"><span>Lorem ipsum dolor sit amet, consectetur ?</span><span>+</span></div><div class="faq-item"><span>Lorem ipsum dolor sit amet, consectetur ?</span><span>+</span></div>
      <div class="faq-item"><span>Lorem ipsum dolor sit amet, consectetur ?</span><span>+</span></div><div class="faq-item"><span>Lorem ipsum dolor sit amet, consectetur ?</span><span>+</span></div>
    </div>

    <div class="abs band" style="top:1795px;height:190px"></div>
    <div class="abs subscribe">
      <div class="abs subscribe-title">SUBSCRIBE<br>NEWSLETTER</div>
      <div class="abs subscribe-field"><span>Enter the Email</span><i><svg width="10" height="10" viewBox="0 0 10 10"><path d="M1 5 9 1 7 9 5 6z" fill="#2f92d5"/></svg></i></div>
    </div>
    <div class="abs footer-brand">VELTRA METRICS</div>
    <div class="abs footer-col" style="left:208px;top:1836px"><h4>QUICK LINKS</h4><ul><li><b>»</b>Home</li><li><b>»</b>About Us</li><li><b>»</b>Services</li><li><b>»</b>Benefits</li><li><b>»</b>Contact Us</li></ul></div>
    <div class="abs footer-col" style="left:310px;top:1836px"><h4>LEGAL</h4><ul><li><b>»</b>Privacy Policy</li><li><b>»</b>GPDR</li><li><b>»</b>Security</li><li><b>»</b>Term of use</li></ul></div>
    <div class="abs footer-col footer-contact" style="left:408px;top:1836px"><h4>CONTACT US</h4><ul>
      <li><svg width="7" height="9" viewBox="0 0 7 9"><path d="M3.5 0A3 3 0 0 0 .5 3c0 2.3 3 6 3 6s3-3.7 3-6a3 3 0 0 0-3-3z" fill="#2f92d5"/></svg><span>123 Lorem ipsum dolor sit amet,<br>consectetur adipiscing</span></li>
      <li style="margin-top:4px"><svg width="8" height="8" viewBox="0 0 8 8"><path d="M1 .5l2 .3.7 1.8-1 .8a5 5 0 0 0 2 2l.8-1 1.8.7.2 2C5 7.5.5 3 1 .5z" fill="#2f92d5"/></svg><span>+ 123 456 7890</span></li>
      <li style="margin-top:6px"><svg width="8" height="7" viewBox="0 0 8 7"><rect width="8" height="7" fill="#2f92d5"/><path d="M0 0l4 3.5L8 0" stroke="#fff" fill="none"/></svg><span>info@veltrametrics.example</span></li></ul></div>
    <div class="abs footer-rule"></div>
    <div class="abs copyright">© Copyrights Veltra Metrics &nbsp;|&nbsp; All Rights Reserved</div>
  </section>

  <!-- Page variant: photographic -->
  <section class="page page--photo">
    <div class="abs nav-logo">VELTRA METRICS</div>
    <nav class="abs nav-links"><span>HOME</span><span>ABOUT US</span><span>SERVICES</span><span>BENEFITS</span><span>CONTACT US</span></nav>
    <div class="abs btn" style="left:460px;top:14px;width:75px;height:24px">COMPARE NOW</div>

    <div class="abs hero-art" role="img" aria-label="Photo from above of colleagues meeting around a table with papers" style="background:linear-gradient(135deg,#8a7a66,#cfc7bd 45%,#3e4450)"></div>
    <h1 class="abs hero-title">Know the Best<br><span class="accent">Health Benefits</span><br>Plan for You!</h1>
    <p class="abs hero-text">Lorem ipsum dolor sit amet, consectetur adipiscing elit,</p>
    <div class="abs btn" style="left:332px;top:229px;width:75px;height:24px">GET STARTED</div>

    <div class="abs label" style="top:342px">OUR BENEFITS</div>
    <h2 class="abs section-title" style="top:355px">Lorem ipsum dolor sit amet, consectetur adipiscing<br>elit, sed do eiusmod tempor incidi.</h2>
    <div class="abs benefits">
      <div class="benefit"><svg width="28" height="24" viewBox="0 0 28 24" fill="none" stroke="#5aa8df" stroke-width="1.2"><path d="M6 14a5 5 0 0 1 2-9 7 7 0 0 1 13 2 4 4 0 0 1 1 7"/><rect x="8" y="12" width="14" height="9"/><path d="M11 16h8"/></svg><h3>LOREM IPSUM DOLOR</h3><p>Lorem ipsum dolor sit amet<br>consectetur adipiscing elit,<br>sed do eiusmod tem.</p></div>
      <div class="benefit benefit--active"><svg width="28" height="24" viewBox="0 0 28 24" fill="none" stroke="#ffffff" stroke-width="1.2"><path d="M6 14a5 5 0 0 1 2-9 7 7 0 0 1 13 2 4 4 0 0 1 1 7"/><rect x="8" y="12" width="14" height="9"/><path d="M11 16h8"/></svg><h3>LOREM IPSUM DOLOR</h3><p>Lorem ipsum dolor sit amet<br>consectetur adipiscing elit,<br>sed do eiusmod tem.</p></div>
      <div class="benefit"><svg width="28" height="24" viewBox="0 0 28 24" fill="none" stroke="#5aa8df" stroke-width="1.2"><path d="M6 14a5 5 0 0 1 2-9 7 7 0 0 1 13 2 4 4 0 0 1 1 7"/><rect x="8" y="12" width="14" height="9"/><path d="M11 16h8"/></svg><h3>LOREM IPSUM DOLOR</h3><p>Lorem ipsum dolor sit amet<br>consectetur adipiscing elit,<br>sed do eiusmod tem.</p></div>
      <div class="benefit"><svg width="28" height="24" viewBox="0 0 28 24" fill="none" stroke="#5aa8df" stroke-width="1.2"><path d="M6 14a5 5 0 0 1 2-9 7 7 0 0 1 13 2 4 4 0 0 1 1 7"/><rect x="8" y="12" width="14" height="9"/><path d="M11 16h8"/></svg><h3>LOREM IPSUM DOLOR</h3><p>Lorem ipsum dolor sit amet<br>consectetur adipiscing elit,<br>sed do eiusmod tem.</p></div>
    </div>

    <div class="abs band" style="top:572px;height:283px"></div>
    <div class="abs label" style="top:617px;left:46px;width:auto;text-align:left">ABOUT VELTRA METRICS</div>
    <h2 class="abs about-title">Lorem ipsum dolor sit amet cons<br>ectetur adipiscing elit sed do.</h2>
    <p class="abs about-text">Lorem ipsum dolor sit amet, consectetur adipiscing elit, sed do eiusmod tempor incididunt ut labore et dolore magna aliqua. Ut enim ad minim veniam, quis nostrud exercitation ullamco laboris nisi ut aliquip ex ea commodo consequat. Duis aute irure dolor in reprehenderit in voluptate velit esse cillum dolore eu fugiat nulla pariatur.</p>
    <div class="abs btn" style="left:46px;top:783px;width:75px;height:24px">READ MORE</div>
    <div class="abs about-art" role="img" aria-label="Photo collage of colleagues talking, a laptop with charts and a team at a desk" style="background:linear-gradient(135deg,#c9b7a6,#eef1f4 50%,#5a6470)"></div>
    <svg class="abs" style="left:347px;top:700px" width="22" height="22" viewBox="0 0 22 22"><circle cx="11" cy="11" r="11" fill="#2f92d5"/><path d="M9 6.5v9l7-4.5z" fill="#fff"/></svg>

    <div class="abs label" style="top:900px">OUR SERVICES</div>
    <h2 class="abs section-title" style="top:913px">Lorem ipsum dolor sit amet, consectetur adipiscing<br>elit, sed do eiusmod tempor incidi.</h2>
    <svg class="abs chevron" style="left:16px" width="18" height="30" viewBox="0 0 18 30" fill="none" stroke="#333" stroke-width="1.3"><path d="M15 2 3 15l12 13"/></svg>
    <svg class="abs chevron" style="left:556px" width="18" height="30" viewBox="0 0 18 30" fill="none" stroke="#333" stroke-width="1.3"><path d="M3 2l12 13L3 28"/></svg>
    <div class="abs services">
      <div class="service"><div class="service-art" role="img" aria-label="Photo of colleagues reviewing documents at a table" style="background:linear-gradient(135deg,#b9a48f,#e7e3dd 55%,#4b4f57)"></div><h3>LOREM IPSUM DOLOR SIT AMET CO<br>NSECTETUR ADIPISCING ELIT</h3><p>Lorem ipsum dolor si amet consectetur<br>adipiscing elit, sed do eiusmod tempor<br>incididunt ut labore et dolore magna.</p><a>READ MORE</a></div>
      <div class="service"><div class="service-art" role="img" aria-label="Photo of a team meeting in a bright office" style="background:linear-gradient(135deg,#e9ecef,#9aa3ad 55%,#3c4048)"></div><h3>LOREM IPSUM DOLOR SIT AMET CO<br>NSECTETUR ADIPISCING ELIT</h3><p>Lorem ipsum dolor si amet consectetur<br>adipiscing elit, sed do eiusmod tempor<br>incididunt ut labore et dolore magna.</p><a>READ MORE</a></div>
      <div class="service"><div class="service-art" role="img" aria-label="Photo of business people discussing at a desk" style="background:linear-gradient(135deg,#5e6670,#c8ccd1 50%,#2f3540)"></div><h3>LOREM IPSUM DOLOR SIT AMET CO<br>NSECTETUR ADIPISCING ELIT</h3><p>Lorem ipsum dolor si amet consectetur<br>adipiscing elit, sed do eiusmod tempor<br>incididunt ut labore et dolore magna.</p><a>READ MORE</a></div>
    </div>

    <div class="abs band" style="top:1224px;height:216px"></div>
    <div class="abs label" style="top:1270px;left:267px;width:auto">TESTIMONIALS</div>
    <h2 class="abs serif" style="left:198px;top:1286px;font-size:16px">What Our People are saying</h2>
    <div class="abs avatar" role="img" aria-label="Portrait photo of a customer" style="background:linear-gradient(135deg,#9a9ea4,#d9c3ad 50%,#4d6fa8)"></div>
    <p class="abs quote">"Lorem ipsum dolor sit amet, consectetur adipiscing elit, sed do eiusmod tempor incididunt ut labore et dolore magna aliqua. Ut enim ad minim veniam, quis nostrud exercitation ullamco laboris nisi ut aliquip ex ea commodo consequat. Duis aute irure dolor in reprehenderit in voluptate velit esse."</p>
    <div class="abs quote-name">RINA CALDER</div>
    <div class="abs dot" style="top:1331px"></div><div class="abs dot dot--open" style="top:1346px"></div><div class="abs dot" style="top:1361px"></div>

    <div class="abs label" style="top:1485px">FAQ</div>
    <h2 class="abs section-title" style="top:1499px">Most asked questions</h2>
    <div class="abs faq">
      <div class="faq-item"><span>Lorem ipsum dolor sit amet, consectetur ?</span><span>+</span></div><div class="faq-item"><span>Lorem ipsum dolor sit amet, consectetur ?</span><span>+</span></div>
      <div class="faq-item"><span>Lorem ipsum dolor sit amet, consectetur ?</span><span>+</span></div><div class="faq-item"><span>Lorem ipsum dolor sit amet, consectetur ?</span><span>+</span></div>
      <div class="faq-item"><span>Lorem ipsum dolor sit amet, consectetur ?</span><span>+</span></div><div class="faq-item"><span>Lorem ipsum dolor sit amet, consectetur ?</span><span>+</span></div>
      <div class="faq-item"><span>Lorem ipsum dolor sit amet, consectetur ?</span><span>+</span></div><div class="faq-item"><span>Lorem ipsum dolor sit amet, consectetur ?</span><span>+</span></div>
      <div class="faq-item"><span>Lorem ipsum dolor sit amet, consectetur ?</span><span>+</span></div><div class="faq-item"><span>Lorem ipsum dolor sit amet, consectetur ?</span><span>+</span></div>
    </div>

    <div class="abs band" style="top:1795px;height:190px"></div>
    <div class="abs subscribe">
      <div class="abs subscribe-title">SUBSCRIBE<br>NEWSLETTER</div>
      <div class="abs subscribe-field"><span>Enter the Email</span><i><svg width="10" height="10" viewBox="0 0 10 10"><path d="M1 5 9 1 7 9 5 6z" fill="#2f92d5"/></svg></i></div>
    </div>
    <div class="abs footer-brand">VELTRA METRICS</div>
    <div class="abs footer-col" style="left:208px;top:1836px"><h4>QUICK LINKS</h4><ul><li><b>»</b>Home</li><li><b>»</b>About Us</li><li><b>»</b>Services</li><li><b>»</b>Benefits</li><li><b>»</b>Contact Us</li></ul></div>
    <div class="abs footer-col" style="left:310px;top:1836px"><h4>LEGAL</h4><ul><li><b>»</b>Privacy Policy</li><li><b>»</b>GPDR</li><li><b>»</b>Security</li><li><b>»</b>Term of use</li></ul></div>
    <div class="abs footer-col footer-contact" style="left:408px;top:1836px"><h4>CONTACT US</h4><ul>
      <li><svg width="7" height="9" viewBox="0 0 7 9"><path d="M3.5 0A3 3 0 0 0 .5 3c0 2.3 3 6 3 6s3-3.7 3-6a3 3 0 0 0-3-3z" fill="#2f92d5"/></svg><span>123 Lorem ipsum dolor sit amet,<br>consectetur adipiscing</span></li>
      <li style="margin-top:4px"><svg width="8" height="8" viewBox="0 0 8 8"><path d="M1 .5l2 .3.7 1.8-1 .8a5 5 0 0 0 2 2l.8-1 1.8.7.2 2C5 7.5.5 3 1 .5z" fill="#2f92d5"/></svg><span>+ 123 456 7890</span></li>
      <li style="margin-top:6px"><svg width="8" height="7" viewBox="0 0 8 7"><rect width="8" height="7" fill="#2f92d5"/><path d="M0 0l4 3.5L8 0" stroke="#fff" fill="none"/></svg><span>info@veltrametrics.example</span></li></ul></div>
    <div class="abs footer-rule"></div>
    <div class="abs copyright">© Copyrights Veltra Metrics &nbsp;|&nbsp; All Rights Reserved</div>
  </section>
</div>
</body>
</html>
```